New Business Card for Web Design/Internet Marketing Company

Looking for a great looking new business card. We are a 10 year old web design, internet marketing and website management company that works mostly with small businesses.

Our new card needs to better match the colors and style of our website, be bold, extremely usable and slightly edgy.

Target Market(s)

Small/Medium businesses that have websites

Industry/Entity Type

Internet

Requirements
Must have
• Front and back design, full color, rounded corners please

Must use the colors/style of our website (JPG provided)

INFO FOR CARDS (as readable as possible please)
Mark Lenner
President/CEO
mark@trelvanmedia.example
Phone: 520-381-7459
Toll Free: 866-381-7459
Address: 4315 W. Calloway Ave. Ste. 140, Tucson, AZ 85792

THINGS I WANT TO PROMOTE (if there is room):
1. Our Website - www.trelvanmedia.example

2. Social Media
Twitter: @trelvanmedia
Facebook: www.facebook.com/trelvanmedia

3. Our Services
Web Design
Internet Marketing
Website Management

```html
<!DOCTYPE html>
<html lang="en">
<head>
<meta charset="utf-8">
<title>Trelvan Media – Business Card</title>
<link rel="stylesheet" href="https://fonts.googleapis.com/css2?family=Open+Sans:wght@400;600;700&display=swap">
<style>
  :root {
    --backdrop: #ebe6df;
    --card-white: #ffffff;
    --brand-blue: #0a8fc8;
    --brand-orange: #f5862e;
    --ink: #4a4a4a;
    --on-color: #ffffff;
  }
  * { box-sizing: border-box; margin: 0; padding: 0; }
  html, body {
    width: 1200px; height: 402px; overflow: hidden;
    background: var(--backdrop);
    font-family: "Open Sans", Arial, sans-serif;
  }
  .canvas { position: relative; width: 1200px; height: 402px; }
  .card {
    position: absolute; top: 57px; width: 512px; height: 290px;
    border-radius: 22px; overflow: hidden;
    box-shadow: 0 3px 10px rgba(0,0,0,.18);
  }
  .card--front { left: 58px; background: var(--card-white); }
  .card--back { left: 629px; background: var(--brand-orange); color: var(--on-color); }

  /* front */
  .wave { position: absolute; left: 0; top: 0; width: 512px; height: 290px; }
  .brand-name {
    position: absolute; left: 30px; top: 88px;
    display: flex; align-items: center; gap: 10px;
    font-weight: 700; font-size: 30px; color: var(--brand-blue); letter-spacing: -0.5px;
  }
  .brand-dot { width: 18px; height: 18px; border-radius: 50%; background: var(--brand-orange); }
  .contact {
    position: absolute; right: 26px; top: 80px; list-style: none;
    font-size: 12px; color: var(--ink); text-align: right; line-height: 17px;
  }
  .contact li { display: flex; justify-content: flex-end; align-items: center; gap: 5px; }
  .contact svg { width: 10px; height: 10px; }
  .address {
    position: absolute; right: 40px; top: 180px;
    font-size: 12px; color: var(--ink); text-align: right; line-height: 15px; font-style: normal;
  }
  .person { position: absolute; left: 62px; top: 226px; color: var(--on-color); text-align: center; }
  .person-name { font-weight: 700; font-size: 19px; line-height: 24px; }
  .person-title { font-size: 14px; line-height: 20px; }

  /* back */
  .back-name {
    position: absolute; left: 36px; top: 128px;
    display: flex; align-items: center; gap: 10px;
    font-weight: 700; font-size: 46px; letter-spacing: -1px;
  }
  .back-dot { width: 22px; height: 22px; border-radius: 50%; background: var(--on-color); }
  .social { position: absolute; left: 272px; top: 40px; list-style: none; font-size: 15px; line-height: 24px; }
  .social li { display: flex; align-items: center; gap: 8px; }
  .social-mark { width: 15px; height: 15px; border-radius: 2px; background: rgba(255,255,255,.85); }
  .services { position: absolute; left: 272px; top: 113px; }
  .services-title { font-weight: 600; font-size: 23px; line-height: 32px; margin-bottom: 10px; }
  .services-list { list-style: none; font-size: 21px; line-height: 31px; }
</style>
</head>
<body>
<main class="canvas">

  <section class="card card--front" aria-label="Card front">
    <svg class="wave" viewBox="0 0 512 290" aria-hidden="true">
      <path d="M0 206 C 40 190, 90 188, 170 200 C 260 214, 330 262, 420 258 C 460 256, 490 246, 512 238 L512 290 L0 290 Z" fill="var(--brand-blue)"/>
      <path d="M34 192 C 110 176, 200 186, 280 212 C 360 236, 430 250, 512 236" fill="none" stroke="var(--brand-orange)" stroke-width="4" stroke-linecap="round"/>
    </svg>

    <div class="brand-name"><span class="brand-dot"></span>Trelvan Media</div>

    <ul class="contact">
      <li>520-381-7459
        <svg viewBox="0 0 10 10"><circle cx="5" cy="5" r="5" fill="var(--brand-blue)"/><path d="M3 2.5 L4.2 2.5 L4.6 4 L4 4.6 Q5 6 5.6 6.2 L6.2 5.6 L7.5 6 L7.5 7.2 Q4 7.5 3 2.5Z" fill="#fff"/></svg></li>
      <li>866-381-7459
        <svg viewBox="0 0 10 10"><circle cx="5" cy="5" r="5" fill="var(--brand-blue)"/><path d="M3 2.5 L4.2 2.5 L4.6 4 L4 4.6 Q5 6 5.6 6.2 L6.2 5.6 L7.5 6 L7.5 7.2 Q4 7.5 3 2.5Z" fill="#fff"/></svg></li>
      <li>mark@trelvanmedia.example
        <svg viewBox="0 0 10 10"><rect x="0.5" y="2" width="9" height="6" fill="var(--brand-blue)"/><path d="M0.5 2 L5 5.5 L9.5 2" fill="none" stroke="#fff" stroke-width="0.8"/></svg></li>
      <li>www.trelvanmedia.example
        <svg viewBox="0 0 10 10"><circle cx="5" cy="5" r="4.5" fill="none" stroke="var(--brand-blue)"/><path d="M0.5 5 H9.5 M5 0.5 V9.5" stroke="var(--brand-blue)" stroke-width="0.8"/></svg></li>
    </ul>

    <address class="address">4315 W. Calloway Ave. Ste. 140<br>Tucson, AZ 85792</address>

    <div class="person">
      <p class="person-name">Mark Lenner</p>
      <p class="person-title">President/CEO</p>
    </div>
  </section>

  <section class="card card--back" aria-label="Card back">
    <div class="back-name"><span class="back-dot"></span>Trelvan</div>

    <ul class="social">
      <li><span class="social-mark"></span>@trelvanmedia</li>
      <li><span class="social-mark"></span>trelvanmedia</li>
    </ul>

    <div class="services">
      <h2 class="services-title">Our Services</h2>
      <ul class="services-list">
        <li>Web Design</li>
        <li>Internet Marketing</li>
        <li>Website Management</li>
      </ul>
    </div>
  </section>

</main>
</body>
</html>
```